Duct Manufacturing Company new to the industry needs business card and stationary design

we are sheet metal duct manufacturers looking for a business card design to fit my new business logo.
nothing to crazy that will date, but want it to stand out from the crowed.
I'm sure you guys will work it out.

Contact Information for Business Card

Glen Marsh
Director

Address
17 Dorwell St
Tallowmere NSW 2715

0438 760 514

Sales@flowbend.com.au

Font styles to use
Other font styles liked:
• BankGothic md bt

Requirements
Nice to have
• Like the idea of corner rounded to match logo
• like to keep colours flowing
• font I like sharp square not rounded

```html
<!DOCTYPE html>
<html lang="en">
<head>
<meta charset="utf-8">
<title>Flowbend Industries – Business Card</title>
<link rel="stylesheet" href="https://fonts.googleapis.com/css2?family=Saira:wght@400;500;600&display=swap">
<style>
  :root {
    --stage: #333333;
    --card-white: #f7f7f7;
    --brand-blue: #0a4fa6;
    --brand-blue-light: #1a78cf;
    --brand-green: #5aab2a;
    --arc-grey: #8c8c8c;
    --text-grey: #555555;
  }
  * { margin: 0; padding: 0; box-sizing: border-box; }
  html, body { width: 1200px; height: 750px; overflow: hidden; }
  body {
    background: var(--stage);
    font-family: "Saira", Arial, sans-serif;
    position: relative;
  }
  .card {
    position: absolute;
    top: 228px;
    width: 461px;
    height: 263px;
    overflow: hidden;
  }
  .card-front { left: 124px; background: var(--card-white); }
  .card-back {
    left: 618px;
    background: radial-gradient(ellipse at 45% 40%, var(--brand-blue-light) 0%, var(--brand-blue) 70%, #0846a0 100%);
  }
  .card-shapes { position: absolute; inset: 0; }
  .brand-name {
    position: absolute;
    left: 36px;
    top: 92px;
    color: var(--brand-blue);
    font-weight: 600;
    font-size: 22px;
    line-height: 1.05;
    letter-spacing: 1px;
    text-transform: uppercase;
    display: flex;
    align-items: center;
    gap: 10px;
  }
  .brand-mark {
    width: 16px; height: 16px;
    background: var(--brand-green);
  }
  .contact {
    position: absolute;
    right: 24px;
    top: 117px;
    text-align: right;
    color: var(--text-grey);
    font-size: 11.5px;
    line-height: 1.3;
  }
  .contact-name { color: var(--brand-blue); font-size: 17px; font-weight: 600; line-height: 1.1; }
  .contact-role { color: var(--brand-green); font-size: 13px; margin-bottom: 6px; }
  .contact-address { margin-bottom: 6px; }
  .contact-line {
    display: flex; justify-content: flex-end; align-items: center; gap: 7px;
    height: 17.5px;
  }
  .contact-line svg { width: 11px; height: 11px; fill: var(--brand-blue); }
  .back-brand {
    position: absolute;
    right: 32px;
    bottom: 22px;
    text-align: center;
    color: #ffffff;
  }
  .back-brand-name { font-size: 19px; font-weight: 600; letter-spacing: 1px; text-transform: uppercase; }
  .back-brand-web { font-size: 11px; margin-top: 4px; }
</style>
</head>
<body>
  <section class="card card-front">
    <svg class="card-shapes" viewBox="0 0 461 263" aria-hidden="true">
      <defs>
        <radialGradient id="cornerBlue" cx="1" cy="0" r="1">
          <stop offset="0" stop-color="#0a4fa6"/>
          <stop offset="1" stop-color="#1a78cf"/>
        </radialGradient>
      </defs>
      <path d="M357 0 Q445 35 461 104 L461 0 Z" fill="url(#cornerBlue)"/>
      <path d="M357 0 Q445 35 461 104" fill="none" stroke="#5aab2a" stroke-width="3"/>
      <path d="M0 160 Q30 235 104 263 L0 263 Z" fill="url(#cornerBlue)"/>
      <path d="M2 160 Q30 235 104 263" fill="none" stroke="#8c8c8c" stroke-width="3"/>
    </svg>
    <div class="brand-name"><span class="brand-mark"></span><span>Flowbend<br>Industries</span></div>
    <div class="contact">
      <p class="contact-name">Glen Marsh</p>
      <p class="contact-role">Director</p>
      <p class="contact-address">17 Dorwell St<br>Tallowmere NSW 2715</p>
      <p class="contact-line">0438 760 514
        <svg viewBox="0 0 24 24"><path d="M6.6 10.8a15 15 0 0 0 6.6 6.6l2.2-2.2c.3-.3.7-.4 1-.2 1.1.4 2.300.6 3.6.6.6 0 1 .4 1 1V20c0 .6-.4 1-1 1A17 17 0 0 1 3 4c0-.6.4-1 1-1h3.5c.6 0 1 .4 1 1 0 1.3.2 2.5.6 3.6.1.3 0 .7-.2 1z"/></svg></p>
      <p class="contact-line">Sales@flowbend.com.au
        <svg viewBox="0 0 24 24"><path d="M2 5h20v14H2z M3 6l9 7 9-7" stroke="#fff" stroke-width="1.5"/></svg></p>
      <p class="contact-line">www.flowbend.com.au
        <svg viewBox="0 0 24 24"><circle cx="12" cy="12" r="10"/><path d="M2 12h20M12 2c3 3 3 17 0 20M12 2c-3 3-3 17 0 20" stroke="#fff" stroke-width="1.3" fill="none"/></svg></p>
    </div>
  </section>

  <section class="card card-back">
    <div class="back-brand">
      <p class="back-brand-name">Flowbend</p>
      <p class="back-brand-web">www.flowbend.com</p>
    </div>
  </section>
</body>
</html>
```